Flyer Design Project

I require a double sided flyer in PSD format.
The flyer should look fresh and clean.
The flyer is for an digital marketing company that offers various services. The services are broken down into 3 main categories and the design should reflect this.
All the content is provided in the attached file
Industry/Entity Type
Digital
Requirements
Must have
- Front of the leaflet to be mainly white background with appealing text based questions in the colours in large font with relevant images.
Back if the
3 separate boxes using the colours indicated in the attachment for the services on back of the leafet.
Should not have
- Gradients
Borders on the edges of the design
Vignettes
Black elements
Any text below 10pt
Fancy fonts
Do not use old-style fonts

```html
<!DOCTYPE html>
<html lang="en">
<head>
<meta charset="utf-8">
<title>Lumora – Flyer Front</title>
<link href="https://fonts.googleapis.com/css2?family=Arimo:wght@400;700&family=Open+Sans:wght@400;600&family=Roboto+Condensed:wght@700&display=swap" rel="stylesheet">
<style>
  :root {
    --slate: #4a5161;
    --slate-deep: #3f4656;
    --white: #ffffff;
    --page: #ececec;
    --green: #9dc43a;
    --blue: #3ab6dc;
    --orange: #f47b20;
    --photo-light: #b3cbe3;
    --photo-dark: #5b6068;
  }
  * { margin: 0; padding: 0; box-sizing: border-box; }
  html, body {
    width: 898px; height: 1200px; overflow: hidden;
    background: var(--page);
  }
  .flyer {
    position: absolute; left: 39px; top: 19px;
    width: 820px; height: 1162px;
    background: var(--white);
    overflow: hidden;
  }
  .header {
    position: absolute; left: 0; top: 0; width: 820px; height: 178px;
    background: var(--slate);
  }
  .brand {
    position: absolute; left: 71px; top: 22px; width: 339px; height: 139px;
    background: var(--slate-deep);
    display: flex; align-items: center; justify-content: center;
  }
  .brand-name {
    font-family: "Open Sans", sans-serif; font-weight: 400;
    font-size: 68px; letter-spacing: 1px; color: var(--blue);
  }
  .contact {
    position: absolute; left: 507px; top: 60px;
    font-family: "Arimo", sans-serif; font-size: 25px; line-height: 31px;
    color: var(--white);
  }
  .contact .accent { color: var(--blue); font-weight: 700; }
  .hero {
    position: absolute; left: 0; top: 188px; width: 820px; height: 403px;
    background: var(--slate);
  }
  .stripe { position: absolute; top: 0; width: 8px; height: 403px; }
  .stripe.green { background: var(--green); }
  .stripe.blue { background: var(--blue); }
  .stripe.orange { background: var(--orange); }
  .hero-photo {
    position: absolute; left: 112px; top: 6px; width: 595px; height: 397px;
    background: linear-gradient(to bottom, var(--photo-light), var(--photo-dark));
  }
  .orange-band {
    position: absolute; left: 0; top: 595px; width: 820px; height: 10px;
    background: var(--orange);
  }
  .questions {
    position: absolute; left: 0; top: 668px; width: 820px;
    text-align: center;
    font-family: "Roboto Condensed", sans-serif; font-weight: 700;
    font-size: 40px; line-height: 42px; letter-spacing: 0.5px;
  }
  .question.green { color: var(--green); }
  .question.blue { color: var(--blue); }
  .question.orange { color: var(--orange); line-height: 48px; }
  .divider {
    width: 323px; height: 4px; margin: 16px auto 18px;
    background: linear-gradient(to right, rgba(58,182,220,0), var(--blue) 50%, rgba(58,182,220,0));
  }
  .footer { position: absolute; left: 0; top: 1026px; width: 820px; height: 136px; }
  .footer svg { position: absolute; left: 0; top: 0; }
  .address {
    position: absolute; left: 0; top: 17px; width: 820px; text-align: center;
    font-family: "Open Sans", sans-serif; font-size: 17px; line-height: 23px;
    color: var(--white);
  }
  .tagline {
    position: absolute; left: 0; top: 84px; width: 820px; text-align: center;
    font-family: "Open Sans", sans-serif; font-size: 26px;
    color: var(--white);
  }
</style>
</head>
<body>
<div class="flyer">
  <header class="header">
    <div class="brand"><span class="brand-name">LUMORA</span></div>
    <div class="contact">
      <p>Call <span class="accent">0121 555 0148</span> for</p>
      <p>a FREE consultation</p>
      <p>www.<span class="accent">lumora</span>.co.uk</p>
    </div>
  </header>

  <section class="hero">
    <span class="stripe green" style="left:25px"></span>
    <span class="stripe blue" style="left:58px"></span>
    <span class="stripe orange" style="left:87px"></span>
    <div class="hero-photo" role="img" aria-label="Photo of a road through green fields rising into the sky as an upward arrow, with WEB TRAFFIC painted on the asphalt"></div>
    <span class="stripe green" style="left:730px"></span>
    <span class="stripe blue" style="left:763px"></span>
    <span class="stripe orange" style="left:791px"></span>
  </section>

  <div class="orange-band"></div>

  <section class="questions">
    <p class="question green">Did You Know 85% of Consumers Use<br>The Internet To Find Businesses Like Yours?</p>
    <div class="divider"></div>
    <p class="question blue">Are Your Customers Finding You Online?</p>
    <div class="divider"></div>
    <p class="question orange">Do You Need More Customers For<br>Your Business?</p>
  </section>

  <footer class="footer">
    <svg width="820" height="136" viewBox="0 0 820 136" aria-hidden="true">
      <polygon points="224,0 605,0 820,83 820,136 0,136 0,83" fill="var(--slate)"/>
    </svg>
    <p class="address">24 Willow Court | 118 Harbour Road<br>Birmingham | B15 4QT | 0121 555 0148</p>
    <p class="tagline">Let us help you grow your business online</p>
  </footer>
</div>
</body>
</html>
```